Brightfen Business Card Redesign & Logo Update

We need to update our business cards to something more modern and fresh. Brightfen can provide the current color schemes and old design examples, but welcome creativity in helping us with this redesign. PLEASE NOTE that we no longer utilize the "tree" and/or "leaf" imagery in our branding. If able would apprecaite an update on the quality of our "words only" logo in Ai. / PNG formats too.

Target Market(s)

Investors, landowners, corporate partners, contractors

Industry/Entity Type

Environmental Restoration & Conservation

Contact Information for Business Card

Logo, persons name, title, mailing address, phone and email, website url

Font styles to use
Other font styles liked:
• Merriweather

Requirements
Nice to have
• Logo, persons name, title, mailing address, phone and email, website url, but open to ideams
Should not have
• No all back backgrounds

```html
<!DOCTYPE html>
<html lang="en">
<head>
<meta charset="utf-8">
<title>Brightfen Business Card</title>
<link rel="stylesheet" href="https://fonts.googleapis.com/css2?family=Bebas+Neue&family=Roboto:wght@400;700&display=swap">
<style>
  :root {
    --orange: #ee7b00;
    --green: #137a32;
    --white: #ffffff;
    --backdrop: #555555;
  }
  * { margin: 0; padding: 0; box-sizing: border-box; }
  html, body { width: 1093px; height: 1200px; overflow: hidden; }
  body { background: var(--backdrop); position: relative; font-family: "Roboto", sans-serif; }

  .card {
    position: absolute;
    left: 264px;
    width: 579px;
    height: 357px;
    border-radius: 24px;
    overflow: hidden;
  }
  .card--front { top: 226px; background: var(--white); }
  .card--back { top: 621px; width: 582px; background: var(--orange); }

  .front-shape { position: absolute; inset: 0; }

  .holder { position: absolute; left: 33px; top: 100px; color: var(--white); }
  .holder__name {
    font-family: "Bebas Neue", sans-serif;
    font-size: 35px; line-height: 1; letter-spacing: -0.3px; font-weight: 400;
  }
  .holder__title { font-size: 16.5px; line-height: 1; margin-top: 3px; }

  .rule { position: absolute; left: 33px; width: 67px; height: 1px; background: var(--white); }
  .rule--top { top: 162px; }
  .rule--bottom { top: 267px; }

  .contacts { position: absolute; left: 33px; top: 176px; list-style: none; color: var(--white); }
  .contacts__item { display: flex; align-items: center; height: 24px; margin-bottom: 3px; font-size: 17px; }
  .contacts__icon {
    width: 24px; height: 24px; background: var(--white);
    display: flex; align-items: center; justify-content: center; margin-right: 4px;
  }

  .address { position: absolute; left: 32px; top: 278px; color: var(--white); font-size: 17px; line-height: 21px; font-style: normal; }

  .brand {
    position: absolute;
    text-align: center;
    font-family: "Roboto", sans-serif;
    font-weight: 700;
    line-height: 1;
  }
  .brand--front { left: 281px; top: 64px; width: 252px; font-size: 46px; color: var(--green); }
  .brand--back { left: 0; width: 582px; top: 146px; font-size: 62px; color: var(--white); }
</style>
</head>
<body>

<section class="card card--front">
  <svg class="front-shape" width="579" height="357" viewBox="0 0 579 357" aria-hidden="true">
    <polygon points="0,0 200,0 361,357 0,357" fill="var(--orange)"/>
    <line x1="202.5" y1="0" x2="363.5" y2="357" stroke="var(--green)" stroke-width="5"/>
  </svg>

  <div class="holder">
    <h1 class="holder__name">Marcus Hale</h1>
    <p class="holder__title">Managing Director</p>
  </div>

  <div class="rule rule--top"></div>

  <ul class="contacts">
    <li class="contacts__item">
      <span class="contacts__icon">
        <svg width="14" height="14" viewBox="0 0 24 24" aria-hidden="true"><path d="M6.6 10.8a15.1 15.1 0 0 0 6.6 6.6l2.2-2.2a1 1 0 0 1 1-.25 11.4 11.4 0 0 0 3.6.57 1 1 0 0 1 1 1V20a1 1 0 0 1-1 1A17 17 0 0 1 3 4a1 1 0 0 1 1-1h3.5a1 1 0 0 1 1 1c0 1.25.2 2.45.57 3.57a1 1 0 0 1-.25 1z" fill="var(--orange)"/></svg>
      </span>
      044-555 210 348
    </li>
    <li class="contacts__item">
      <span class="contacts__icon">
        <svg width="16" height="12" viewBox="0 0 16 12" aria-hidden="true"><rect x="0.75" y="0.75" width="14.5" height="10.5" fill="none" stroke="var(--orange)" stroke-width="1.3"/><path d="M1 1l7 6 7-6" fill="none" stroke="var(--orange)" stroke-width="1.3"/></svg>
      </span>
      hello@brightfen.com
    </li>
    <li class="contacts__item">
      <span class="contacts__icon">
        <svg width="15" height="15" viewBox="0 0 16 16" aria-hidden="true"><g fill="none" stroke="var(--orange)" stroke-width="1.2"><circle cx="8" cy="8" r="6.8"/><ellipse cx="8" cy="8" rx="3" ry="6.8"/><path d="M1.2 8h13.6M2.3 4.5h11.4M2.3 11.5h11.4"/></g></svg>
      </span>
      www.brightfen.com
    </li>
  </ul>

  <div class="rule rule--bottom"></div>

  <address class="address">
    18 Marsh Lane, Suite 4<br>
    30718, Fenland
  </address>

  <p class="brand brand--front">Brightfen</p>
</section>

<section class="card card--back">
  <p class="brand brand--back">Brightfen</p>
</section>

</body>
</html>
```